Upstart Retirement Planning Firm needs help with business card design

Harborview Nest Advisors, LLC is looking for help with business card design. We give advice on investments, insurance, and other financial matters related to retirement. There are some required disclosures that we will provide but mostly we are looking for a professional, classy business card that reflects the theme we have chosen. We have a logo that is attached but we would like to add a phrase; "Building Today's Paychecks Into Tomorrow's Security"

Doubled sided only so that we can add the required disclosures (needed for our industry) on the back of the card. We will provide the exact words for this in 1-2 days.

Target Market(s)

Retirees and Pre-retirees. Professionals 50+ years old

Industry/Entity Type

Financial Planning

Contact Information for Business Card

We currently have two people who will need separate cards so we'd like to have a template so that we can add names for new cards in the future.

For the first run, please show the following information.

Gregor Pelham, MBA, CRA, WMS
Financial Advisor, Registered Representative
gpelham@harborviewnest.example
Phone: (555) 318-2946
Toll Free Fax: (800) 555-0193

Address is
2187 Meadowlark Ridge Rd.
Suite K418
Bayhollow, VA 23999

Colors
3277b5

Requirements
Must have
• Logo, contact info, small phase to describe business (in description), required legal disclosures on back of the card as follows (in small font)
• Gregor Pelham is a registered representative of and offers securities through Brightmoor Capital Brokerage Corporation, Member FNQX. Brightmoor Capital Brokerage Corporation is a member of the Brightmoor Capital Alliance which is the marketing name for Brightmoor Holding Corporation and its affiliates.
Nice to have
• Rounded edges, raised letters
Should not have
• any colors that aren't in the logo (other than black for font)

```html
<!DOCTYPE html>
<html lang="en">
<head>
<meta charset="utf-8">
<title>Harborview Nest Advisors – Business Card</title>
<link href="https://fonts.googleapis.com/css2?family=Arimo:wght@400;700&display=swap" rel="stylesheet">
<style>
  :root {
    --brand-blue: #1f6fb8;
    --brand-blue-deep: #1865ad;
    --ink: #1d1d1d;
    --ink-soft: #333;
    --paper: #ffffff;
    --backdrop: #e9eaec;
    --rule-grey: #9a9a9a;
  }
  * { box-sizing: border-box; margin: 0; padding: 0; }
  html, body { width: 1200px; height: 750px; overflow: hidden; }
  body {
    background: var(--backdrop);
    font-family: "Arimo", Arial, sans-serif;
    color: var(--ink);
    position: relative;
  }
  .card {
    position: absolute;
    top: 221px;
    width: 540px;
    height: 308px;
    border-radius: 18px;
    overflow: hidden;
    box-shadow: 0 6px 18px rgba(0,0,0,0.18);
  }
  .card--front { left: 40px; background: var(--brand-blue); }
  .card--back { left: 620px; background: var(--paper); }

  .front-brand {
    position: absolute; inset: 0;
    display: flex; align-items: center; justify-content: center; gap: 14px;
    color: var(--paper);
    font-size: 30px; font-weight: 700;
  }
  .front-brand .brand-dot {
    width: 22px; height: 22px; border-radius: 50%; background: var(--paper);
  }

  .back-brand {
    position: absolute; left: 28px; top: 112px; width: 190px;
    color: var(--brand-blue);
    font-size: 21px; font-weight: 700; line-height: 1.2;
  }
  .back-brand .brand-rule {
    display: block; margin-top: 10px; height: 1px; width: 170px; background: var(--rule-grey);
  }

  .contact {
    position: absolute; left: 245px; top: 28px; width: 285px;
    font-size: 12.5px; line-height: 1.35; color: var(--ink-soft);
  }
  .contact__name {
    color: var(--brand-blue); font-size: 21px; font-weight: 700; white-space: nowrap;
  }
  .contact__creds { font-size: 10.5px; font-weight: 700; vertical-align: 6px; }
  .contact__role { margin-top: 2px; }
  .contact__address { margin-top: 14px; font-size: 13.5px; }
  .contact__lines { margin-top: 10px; list-style: none; font-size: 13.5px; }
  .contact__lines li { display: flex; align-items: center; gap: 7px; white-space: nowrap; }
  .contact__lines svg { width: 13px; height: 13px; fill: var(--brand-blue-deep); flex: none; }

  .tagline-rule {
    position: absolute; left: 0; right: 0; bottom: 54px; height: 6px; background: var(--brand-blue);
  }
  .tagline-band {
    position: absolute; left: 0; right: 0; bottom: 0; height: 48px;
    background: var(--brand-blue);
    color: var(--paper); font-size: 16px;
    display: flex; align-items: center; justify-content: center;
  }
</style>
</head>
<body>
  <section class="card card--front" aria-label="Card front">
    <div class="front-brand">
      <span class="brand-dot"></span>
      <span>Harborview Nest Advisors</span>
    </div>
  </section>

  <section class="card card--back" aria-label="Card back">
    <div class="back-brand">
      Harborview Nest Advisors, LLC
      <span class="brand-rule"></span>
    </div>

    <div class="contact">
      <div class="contact__name">Gregor Pelham, <span class="contact__creds">MBA, CRA, WMS</span></div>
      <div class="contact__role">Financial Advisor<br>Registered Representative</div>
      <div class="contact__address">2187 Meadowlark Ridge Rd.<br>Suite K418<br>Bayhollow, VA 23999</div>
      <ul class="contact__lines">
        <li><svg viewBox="0 0 24 24"><path d="M6.6 10.8a15.1 15.1 0 0 0 6.6 6.6l2.2-2.2a1 1 0 0 1 1-.25 11.4 11.4 0 0 0 3.6.57 1 1 0 0 1 1 1V20a1 1 0 0 1-1 1A17 17 0 0 1 3 4a1 1 0 0 1 1-1h3.5a1 1 0 0 1 1 1c0 1.25.2 2.45.57 3.57a1 1 0 0 1-.25 1z"/></svg>(555) 318-2946</li>
        <li><svg viewBox="0 0 24 24"><path d="M6.6 10.8a15.1 15.1 0 0 0 6.6 6.6l2.2-2.2a1 1 0 0 1 1-.25 11.4 11.4 0 0 0 3.6.57 1 1 0 0 1 1 1V20a1 1 0 0 1-1 1A17 17 0 0 1 3 4a1 1 0 0 1 1-1h3.5a1 1 0 0 1 1 1c0 1.25.2 2.45.57 3.57a1 1 0 0 1-.25 1z"/></svg>(800) 555-0193 (Toll Free)</li>
        <li><svg viewBox="0 0 24 24"><path d="M3 6l9 7 9-7v12H3z"/><path d="M3 5h18l-9 7z"/></svg>gpelham@harborviewnest.example</li>
      </ul>
    </div>

    <div class="tagline-rule"></div>
    <div class="tagline-band">Building Today's Paychecks Into Tomorrow's Security</div>
  </section>
</body>
</html>
```